Business Card Design

It's an investment advisory service for individuals with all there investment needs. Also financial consulting to businesses and governmental agencies on retirement plans etc. It's personalized not commoditized help. Should show strength, knowledge and money orientation.

Reason: Will be out of town setting up office.

Reason: waiting for the 2/3rds of group to vote

Reason: only half the votes are in, I'm calling and getting verbals, but at this time we are down to 2 designs.

Industry/Entity Type

Investment

Contact Information for Business Card

B. Rel K. Financial Consulting and Wealth Management, Berislav Mike Holcek, 5172 Pasadena Loma Verde, San Diego, CA 94417-6381, Registered Investment Advisor

Requirements
Nice to have
• Something money oriented

```html
<!DOCTYPE html>
<html lang="en">
<head>
<meta charset="utf-8">
<title>B. Rel K. Business Card</title>
<link href="https://fonts.googleapis.com/css2?family=Crimson+Pro:wght@400;600;700&display=swap" rel="stylesheet">
<style>
  :root {
    --backdrop: #181818;
    --frame-line: #262626;
    --brand-green: #134a2a;
    --deep-green: #1f5a33;
    --mid-green: #4f8a5c;
    --soft-green: #8fb596;
    --pale: #f7faf7;
    --ink: #1e1e1e;
    --accent-green: #3d7a4c;
    --white: #ffffff;
  }
  * { margin: 0; padding: 0; box-sizing: border-box; }
  html, body {
    width: 1200px; height: 1000px; overflow: hidden;
    background: var(--backdrop);
    font-family: "Crimson Pro", Georgia, serif;
  }
  .stage { position: relative; width: 1200px; height: 1000px; }
  .presentation-frame {
    position: absolute; left: 134px; top: 197px;
    width: 941px; height: 548px;
    border: 1px solid var(--frame-line);
  }
  .card {
    position: absolute; left: 152px; top: 215px;
    width: 904px; height: 514px; overflow: hidden;
    background:
      radial-gradient(ellipse 48% 42% at 62% 50%, var(--white) 0%, rgba(255,255,255,0.85) 45%, rgba(255,255,255,0) 100%),
      linear-gradient(180deg, var(--mid-green) 0%, #b9d0bc 22%, var(--pale) 45%, #e9f0ea 62%, var(--soft-green) 80%, var(--deep-green) 100%);
  }
  .card::before {
    content: ""; position: absolute; inset: 0;
    background: linear-gradient(90deg, rgba(31,90,51,0.45) 0%, rgba(31,90,51,0) 30%, rgba(31,90,51,0) 80%, rgba(31,90,51,0.25) 100%);
  }
  .banknote-edge {
    position: absolute; top: 0; width: 44px; height: 100%;
    background: linear-gradient(180deg, #8aa883 0%, #b7c8ae 40%, #6f8f68 75%, #3f6a45 100%);
  }
  .banknote-edge.left { left: 0; }
  .banknote-edge.right { right: 0; }
  .brand-block {
    position: absolute; left: 0; top: 53px;
    width: 300px; height: 284px;
    background: var(--brand-green);
    display: flex; align-items: center; justify-content: center;
    padding: 0 28px;
  }
  .brand-name {
    color: var(--white); font-weight: 400; text-align: center;
    font-size: 24px; line-height: 1.35;
    text-transform: uppercase; letter-spacing: 0.04em;
  }
  .contact {
    position: absolute; right: 79px; top: 66px; text-align: right;
  }
  .person-name { font-size: 42px; font-weight: 700; color: var(--ink); line-height: 1.1; }
  .credentials { font-size: 25px; color: var(--accent-green); margin-top: 2px; line-height: 1.1; }
  .phone, .email { font-size: 34px; color: var(--ink); line-height: 1.2; }
  .phone { margin-top: 4px; display: flex; align-items: center; justify-content: flex-end; gap: 8px; }
  .phone-icon { width: 26px; height: 26px; }
  .market-art {
    position: absolute; left: 408px; top: 262px;
    width: 396px; height: 192px;
    background: radial-gradient(ellipse 50% 55% at 50% 55%, rgba(60,110,70,0.75) 0%, rgba(90,140,100,0.45) 55%, rgba(255,255,255,0) 100%);
  }
  .designation {
    position: absolute; left: 0; right: 0; top: 463px;
    text-align: center; color: var(--white);
    font-size: 22px; letter-spacing: 0.62em; text-transform: uppercase;
    padding-left: 0.62em;
  }
</style>
</head>
<body>
<main class="stage">
  <div class="presentation-frame"></div>
  <section class="card">
    <div class="banknote-edge left" role="img" aria-label="Engraved banknote border pattern"></div>
    <div class="banknote-edge right" role="img" aria-label="Engraved banknote border pattern"></div>

    <div class="brand-block">
      <div class="brand-name">B. Rel K. Financial Consulting &amp; Wealth Management</div>
    </div>

    <div class="contact">
      <div class="person-name">Berislav “Mike” Holcek</div>
      <div class="credentials">MBA, RP©, CRC©</div>
      <div class="phone">
        <svg class="phone-icon" viewBox="0 0 26 26" aria-hidden="true">
          <circle cx="13" cy="13" r="11.5" fill="none" stroke="var(--accent-green)" stroke-width="1.6"/>
          <path d="M9 7.5c-1.4 1.2-1.6 3.4 0 6.4s3.6 4.8 5.6 4.8c1 0 1.8-.6 2.2-1.2l-2.2-2.2-1.3.8c-1-.5-2.3-2-2.8-3.3l.9-1.1L9 7.5z" fill="var(--accent-green)"/>
        </svg>
        <span>858-555-0147 / 775-555-0192</span>
      </div>
      <div class="email">mike.holcek@relkmail.com</div>
    </div>

    <div class="market-art" role="img" aria-label="Engraved bull and bear facing each other, green tones"></div>

    <div class="designation">Registered Investment Advisor</div>
  </section>
</main>
</body>
</html>
```